Dental office stationary (letterhead, envelopes), business cards, presentation folders

Nothing too dental outside of the logo. I will need all stationary, presentation folders, business cards. Would prefer to stay in the colors of the logo

Gordon Patel, DDS
Bright Haven Dental Implant Center
555-318-2790
info@brighthavendental.example
4817 NW Maple Crest Rd Unit B
Stuart, FL 00000

Also need appointment date and time
And cancellation policy
I want it to say “kindly ask for
A 48hr cancellation policy to avoid incurring a cancellation fee”

Industry/Entity Type

Dental

Colors
0054AA
0677BA
7BADD7
CADEEF
E8F1F8

Requirements
Must have
• Name of your office, name of doctor, address, phone number
Should not have
• Too much tooth/dental. Only the tooth in logo

```html
<!DOCTYPE html>
<html lang="en">
<head>
<meta charset="utf-8">
<title>Bright Haven Dental Implant Center – Business and Appointment Cards</title>
<link rel="stylesheet" href="https://fonts.googleapis.com/css2?family=Cinzel:wght@500&family=Roboto:wght@400;500;700&display=swap">
<style>
  :root {
    --bg: #e4e4e2;
    --card: #ffffff;
    --ink: #2b2b2b;
    --rule: #8a8a8a;
    --blue: #0677ba;
    --blue-deep: #0054aa;
    --blue-light: #0a8ad0;
    --teal: #12a08a;
  }
  * { box-sizing: border-box; margin: 0; padding: 0; }
  html, body { width: 1200px; height: 801px; overflow: hidden; background: var(--bg); }
  .stage { position: relative; width: 1200px; height: 801px; }

  .card {
    position: absolute; top: 246px; width: 540px; height: 309px;
    background: var(--card);
    box-shadow: 0 6px 18px rgba(0,0,0,.18);
    overflow: hidden;
  }
  .card--front { left: 40px; }
  .card--back { left: 620px; display: flex; }

  /* front */
  .brand {
    position: absolute; left: 28px; top: 0; width: 206px; height: 100%;
    display: flex; align-items: center; gap: 9px;
  }
  .brand__dot { width: 12px; height: 12px; border-radius: 50%; background: var(--blue); flex: none; }
  .brand__name {
    font-family: "Cinzel", serif; font-weight: 500; font-size: 21px;
    color: var(--blue); white-space: nowrap;
  }
  .divider { position: absolute; left: 246px; top: 64px; width: 1px; height: 180px; background: var(--rule); }
  .contact {
    position: absolute; left: 264px; top: 66px;
    font-family: "Roboto", sans-serif; color: var(--ink); font-size: 13px; line-height: 1.45;
  }
  .contact__name { font-weight: 700; font-size: 17px; color: var(--blue); margin-bottom: 1px; }
  .contact__name span { color: var(--teal); }
  .contact__office { margin-bottom: 10px; }
  .contact__address { margin-bottom: 12px; }
  .contact__row { display: flex; align-items: center; gap: 7px; }
  .contact__row svg { width: 12px; height: 12px; flex: none; fill: var(--teal); }
  .contact__web-accent { color: var(--teal); }

  /* back */
  .band {
    width: 152px; height: 100%;
    background: linear-gradient(160deg, var(--blue-deep) 0%, var(--blue-light) 55%, var(--blue) 100%);
    position: relative;
  }
  .band__brand {
    position: absolute; left: 50%; top: 50%;
    transform: translate(-50%, -50%) rotate(-90deg);
    display: flex; align-items: center; gap: 10px; white-space: nowrap;
  }
  .band__dot { width: 14px; height: 14px; border-radius: 50%; background: #fff; }
  .band__name { font-family: "Cinzel", serif; font-weight: 500; font-size: 26px; color: #fff; }

  .appointment { flex: 1; padding: 46px 30px 0 34px; }
  .appointment__title {
    font-family: "Cinzel", serif; font-weight: 500; font-size: 26px;
    color: var(--teal); letter-spacing: 1.5px; text-align: center; margin-bottom: 30px;
  }
  .field { display: flex; align-items: flex-end; gap: 8px; margin-bottom: 34px;
    font-family: "Roboto", sans-serif; font-size: 15px; color: var(--ink); }
  .field__label { white-space: nowrap; }
  .field__line { flex: 1; border-bottom: 1px solid var(--rule); height: 1px; margin-bottom: 4px; }
</style>
</head>
<body>
<main class="stage">

  <section class="card card--front" aria-label="Business card front">
    <div class="brand">
      <span class="brand__dot"></span>
      <span class="brand__name">Bright Haven</span>
    </div>
    <div class="divider"></div>
    <div class="contact">
      <p class="contact__name">Gordon <span>Patel, DDS</span></p>
      <p class="contact__office">Bright Haven Dental Implant Center</p>
      <p class="contact__address">4817 NW Maple Crest Rd Unit B<br>Lakeside, XX 00000</p>
      <p class="contact__row">
        <svg viewBox="0 0 24 24" aria-hidden="true"><path d="M6.6 10.8a15 15 0 0 0 6.6 6.6l2.2-2.2a1 1 0 0 1 1-.25 11.4 11.4 0 0 0 3.6.57 1 1 0 0 1 1 1V20a1 1 0 0 1-1 1A17 17 0 0 1 3 4a1 1 0 0 1 1-1h3.5a1 1 0 0 1 1 1c0 1.25.2 2.45.57 3.57a1 1 0 0 1-.25 1z"/></svg>
        <span>555-318-2790</span>
      </p>
      <p class="contact__row">
        <svg viewBox="0 0 24 24" aria-hidden="true"><path d="M2 5h20v14H2zm2 2v.5l8 5 8-5V7l-8 5z"/></svg>
        <span>info@brighthavendental.example</span>
      </p>
      <p class="contact__row">
        <svg viewBox="0 0 24 24" aria-hidden="true"><circle cx="12" cy="12" r="10"/></svg>
        <span>www.<span class="contact__web-accent">brighthavendental</span>.example</span>
      </p>
    </div>
  </section>

  <section class="card card--back" aria-label="Appointment card">
    <div class="band">
      <div class="band__brand">
        <span class="band__dot"></span>
        <span class="band__name">Bright Haven</span>
      </div>
    </div>
    <div class="appointment">
      <h2 class="appointment__title">APPOINTMENT</h2>
      <p class="field"><span class="field__label">Name :</span><span class="field__line"></span></p>
      <p class="field"><span class="field__label">DATE :</span><span class="field__line"></span></p>
      <p class="field"><span class="field__label">TIME :</span><span class="field__line"></span></p>
    </div>
  </section>

</main>
</body>
</html>
```